Vantro cards

I am in the auto motive, transportation business I would like a business card that is Something cool, modern edgy, having to do with car culture. I offer towing service for high and exotic cars. I also provide towing for collisions and car accidents. I offer open and enclosed transport nationwide.

Target Market(s)

Car culture people high end auto collectors

Industry/Entity Type

Towing car carrier

Contact Information for Business Card

My company colors black yellow and silver

Font styles to use
Serif

```html
<!DOCTYPE html>
<html lang="en">
<head>
<meta charset="utf-8">
<title>Vantro Business Cards</title>
<link rel="stylesheet" href="https://fonts.googleapis.com/css2?family=Bebas+Neue&family=Poppins:wght@400;700&display=swap">
<style>
  :root {
    --stage: #1c1c1c;
    --card: #111111;
    --yellow: #f9dd52;
    --white: #ffffff;
    --rule: #8a8a8a;
  }
  * { margin: 0; padding: 0; box-sizing: border-box; }
  html, body {
    width: 1200px;
    height: 900px;
    overflow: hidden;
    background: var(--stage);
  }
  .stage {
    position: relative;
    width: 1200px;
    height: 900px;
  }
  .card {
    position: absolute;
    left: 280px;
    width: 640px;
    height: 366px;
    background: var(--card);
    overflow: hidden;
    box-shadow: 0 12px 30px rgba(0,0,0,0.55);
  }
  .card::after {
    content: "";
    position: absolute;
    left: 0; right: 0; bottom: 0;
    height: 12px;
    background: var(--yellow);
  }
  .card--front { top: 56px; }
  .card--back { top: 462px; }

  .brand {
    position: absolute;
    left: 0; right: 0; top: 0; bottom: 12px;
    display: flex;
    align-items: center;
    justify-content: center;
    gap: 18px;
  }
  .brand__dot {
    width: 34px;
    height: 34px;
    border-radius: 50%;
    background: var(--yellow);
  }
  .brand__name {
    font-family: "Poppins", sans-serif;
    font-weight: 700;
    font-size: 64px;
    letter-spacing: 4px;
    color: var(--white);
    text-transform: uppercase;
  }

  .person {
    position: absolute;
    left: 62px;
    top: 140px;
  }
  .person__name {
    font-family: "Bebas Neue", sans-serif;
    font-size: 44px;
    line-height: 1;
    color: var(--yellow);
    letter-spacing: 0.5px;
  }
  .person__role {
    font-family: "Poppins", sans-serif;
    font-size: 16px;
    color: var(--white);
    margin-top: 2px;
  }
  .divider {
    position: absolute;
    left: 300px;
    top: 140px;
    width: 1px;
    height: 92px;
    background: var(--rule);
  }
  .contact {
    position: absolute;
    left: 326px;
    top: 146px;
    list-style: none;
    font-family: "Poppins", sans-serif;
    font-size: 17px;
    color: var(--white);
  }
  .contact__item {
    display: flex;
    align-items: center;
    gap: 10px;
    height: 28px;
  }
  .contact__icon {
    width: 18px;
    height: 18px;
    flex: none;
  }
  .address {
    position: absolute;
    left: 62px;
    bottom: 40px;
    font-family: "Poppins", sans-serif;
    font-size: 16px;
    color: var(--white);
  }
</style>
</head>
<body>
<main class="stage">
  <section class="card card--front" aria-label="Card front">
    <div class="brand">
      <span class="brand__dot"></span>
      <span class="brand__name">Vantro</span>
    </div>
  </section>

  <section class="card card--back" aria-label="Card back">
    <div class="person">
      <h1 class="person__name">MARCUS HALE</h1>
      <p class="person__role">Managing Director</p>
    </div>
    <div class="divider"></div>
    <ul class="contact">
      <li class="contact__item">
        <svg class="contact__icon" viewBox="0 0 24 24" aria-hidden="true">
          <path d="M6.6 10.8a15.1 15.1 0 0 0 6.6 6.6l2.2-2.2a1 1 0 0 1 1-.25 11.4 11.4 0 0 0 3.6.57 1 1 0 0 1 1 1V20a1 1 0 0 1-1 1A17 17 0 0 1 3 4a1 1 0 0 1 1-1h3.5a1 1 0 0 1 1 1c0 1.25.2 2.45.57 3.57a1 1 0 0 1-.25 1z" fill="var(--yellow)"/>
        </svg>
        <span>044-987 650 321</span>
      </li>
      <li class="contact__item">
        <svg class="contact__icon" viewBox="0 0 24 24" aria-hidden="true">
          <rect x="2" y="5" width="20" height="14" fill="var(--yellow)"/>
          <path d="M2 5l10 8 10-8" fill="none" stroke="var(--card)" stroke-width="1.6"/>
        </svg>
        <span>hello@vantromail.com</span>
      </li>
      <li class="contact__item">
        <svg class="contact__icon" viewBox="0 0 24 24" aria-hidden="true">
          <g fill="none" stroke="var(--yellow)" stroke-width="2">
            <circle cx="12" cy="12" r="9.5"/>
            <ellipse cx="12" cy="12" rx="4" ry="9.5"/>
            <path d="M2.5 12h19M4 7h16M4 17h16"/>
          </g>
        </svg>
        <span>www.vantrohaul.com</span>
      </li>
    </ul>
    <p class="address">88, Harbor Road, Eastvale, 30718</p>
  </section>
</main>
</body>
</html>
```